Heron Loan Partners Business Card

We need a business card design for our mortgage servicing company. In addition to servicing the loans of homeowners, we help homeowners with purchasing their homes and any mortgage refinancing. We would like to see designs that use the colors in the logo attached below (gold-ish yellow and navy blue), and any other design you deem fit! The design should communicate a simpler life with smart mortgages provided by Heron.

```html
<!DOCTYPE html>
<html lang="en">
<head>
<meta charset="utf-8">
<title>Heron Loan Partners Business Card</title>
<link rel="stylesheet" href="https://fonts.googleapis.com/css2?family=Open+Sans:wght@400;600;700&display=swap">
<style>
  :root {
    --gold: #e2b236;
    --navy: #2a2460;
    --ink: #1d1d22;
    --paper: #ffffff;
    --backdrop: #e9eaee;
  }
  * { margin: 0; padding: 0; box-sizing: border-box; }
  html, body { width: 1200px; height: 780px; overflow: hidden; }
  body {
    background: var(--backdrop);
    font-family: "Open Sans", Arial, sans-serif;
    color: var(--ink);
  }
  .canvas {
    position: relative;
    width: 1200px;
    height: 780px;
    display: flex;
    align-items: center;
    justify-content: center;
    gap: 40px;
  }
  .card {
    position: relative;
    width: 540px;
    height: 310px;
    background: var(--paper);
    border-radius: 16px;
    overflow: hidden;
    box-shadow: 0 10px 28px rgba(20, 20, 40, 0.18);
  }
  .edge-band {
    position: absolute;
    left: 0; bottom: 0;
    width: 100%;
    height: 34px;
  }
  /* front */
  .brand {
    position: absolute;
    display: flex;
    align-items: center;
    gap: 12px;
    color: var(--navy);
    font-weight: 700;
    white-space: nowrap;
  }
  .brand-dot {
    border-radius: 50%;
    background: var(--gold);
    flex: none;
  }
  .card--front .brand {
    left: 0; right: 0; top: 112px;
    justify-content: center;
    font-size: 34px;
  }
  .card--front .brand-dot { width: 30px; height: 30px; }
  /* back */
  .card--back .brand {
    left: 32px; top: 34px;
    font-size: 19px;
    gap: 8px;
  }
  .card--back .brand-dot { width: 18px; height: 18px; }
  .divider {
    position: absolute;
    left: 178px; top: 92px;
    width: 66px; height: 136px;
  }
  .contact-block {
    position: absolute;
    left: 268px; top: 96px;
  }
  .person-name {
    font-size: 25px;
    font-weight: 700;
    line-height: 1.1;
    letter-spacing: 0.3px;
    white-space: nowrap;
  }
  .person-name .first { color: var(--gold); }
  .person-name .last { color: var(--navy); }
  .person-role {
    font-size: 14px;
    margin-top: 4px;
    margin-bottom: 12px;
    letter-spacing: 0.4px;
  }
  .contact-list { list-style: none; }
  .contact-list li {
    display: flex;
    align-items: center;
    gap: 8px;
    font-size: 13px;
    line-height: 22px;
    white-space: nowrap;
  }
  .contact-icon { width: 14px; height: 14px; flex: none; }
  .address {
    position: absolute;
    left: 32px; bottom: 46px;
    font-size: 13px;
    letter-spacing: 0.3px;
    white-space: nowrap;
  }
</style>
</head>
<body>
  <main class="canvas">

    <section class="card card--front" aria-label="Card front">
      <div class="brand">
        <span class="brand-dot"></span>
        <span class="brand-name">Heron Loan Partners</span>
      </div>
      <svg class="edge-band" viewBox="0 0 540 34" preserveAspectRatio="none" aria-hidden="true">
        <rect x="0" y="12" width="226" height="22" fill="var(--gold)"/>
        <polygon points="234,34 240,4 540,4 540,34" fill="var(--navy)"/>
      </svg>
    </section>

    <section class="card card--back" aria-label="Card back">
      <div class="brand">
        <span class="brand-dot"></span>
        <span class="brand-name">Heron Loan Partners</span>
      </div>

      <svg class="divider" viewBox="0 0 66 136" aria-hidden="true">
        <line x1="64" y1="2" x2="2" y2="134" stroke="var(--ink)" stroke-width="1.2"/>
      </svg>

      <div class="contact-block">
        <h1 class="person-name"><span class="first">Dana</span> <span class="last">Kovalova</span></h1>
        <p class="person-role">Managing Director</p>
        <ul class="contact-list">
          <li>
            <svg class="contact-icon" viewBox="0 0 16 16" aria-hidden="true">
              <path d="M4 1.5l2.2 3-1.4 1.6c.8 1.8 2.2 3.3 4.1 4.1L10.5 8.8l3 2.2-1.2 2.6C7 13.4 2.6 9 2.4 3.7z" fill="var(--gold)"/>
            </svg>
            <span>(555) 014-2290</span>
          </li>
          <li>
            <svg class="contact-icon" viewBox="0 0 16 16" aria-hidden="true">
              <rect x="1" y="3" width="14" height="10" rx="1.5" fill="var(--gold)"/>
              <path d="M1.8 4l6.2 4.8L14.2 4" fill="none" stroke="#fff" stroke-width="1.2"/>
            </svg>
            <span>info@heronloanpartners.com</span>
          </li>
          <li>
            <svg class="contact-icon" viewBox="0 0 16 16" aria-hidden="true">
              <circle cx="8" cy="8" r="7" fill="var(--gold)"/>
              <path d="M1 8h14M8 1c-2.6 3-2.6 11 0 14M8 1c2.6 3 2.6 11 0 14" fill="none" stroke="#fff" stroke-width="1"/>
            </svg>
            <span>www.heronloanpartners.com</span>
          </li>
        </ul>
      </div>

      <p class="address">1840 Lakeshore Ave. Suite 300 Cedar Falls, TX 75001</p>

      <svg class="edge-band" viewBox="0 0 540 34" preserveAspectRatio="none" aria-hidden="true">
        <rect x="0" y="12" width="226" height="22" fill="var(--gold)"/>
        <polygon points="234,34 240,4 540,4 540,34" fill="var(--navy)"/>
      </svg>
    </section>

  </main>
</body>
</html>
```